Flyer for the Radiant Harvest Worship Day

I am looking to create a flyer for a one day prayer retreat our church is organizing.
This flyer will be posted on social media, websites and will also be printed so it can be mailed to people.
I am looking for something professional, with good use of our logo and band colors (logo colors).
I am counting on the designer's skill, creativity, art and knowledge of media communication to produce a flyer that will effectively and quickly convey the message we are trying to spread.
CONTENT OF THE FLYER:
Event title: Radiant Harvest Worship Day
Date: Tuesday July 2nd, 2019
Time: 11:00AM - 7:00PM
Belmora Hotel, 4875 Wexley Avenue, Portland, Maine 04102 (Room: Juniper)
Event Key words to highlight what the event is about: Prayer, Sharing the Word, Panel discussion, prophecy, Impartation.
Key phrases:
A one day prayer retreat.
Jesus Chris is Lord
Contact info:
www.tolvex.org
Phone: 207 555 3184
Email: contact@brookhavenfold.org

```html
<!DOCTYPE html>
<html lang="en">
<head>
<meta charset="utf-8">
<title>Radiant Harvest Worship Day</title>
<link rel="stylesheet" href="https://fonts.googleapis.com/css2?family=Dosis:wght@400;500&display=swap">
<style>
  :root {
    --navy: #003a5c;
    --orange: #f7941d;
    --white: #ffffff;
    --ink: #0b3455;
  }
  html, body {
    margin: 0;
    padding: 0;
    width: 846px;
    height: 1200px;
    overflow: hidden;
    background: var(--navy);
  }
  .flyer {
    position: relative;
    width: 846px;
    height: 1200px;
    overflow: hidden;
    font-family: "Dosis", sans-serif;
    font-weight: 400;
  }
  .flyer div, .flyer h1 { white-space: nowrap; }
  .backdrop {
    position: absolute;
    inset: 0;
    width: 846px;
    height: 1200px;
  }
  .brand {
    position: absolute;
    top: 110px;
    left: 400px;
    display: flex;
    align-items: center;
    gap: 14px;
  }
  .brand-dot {
    width: 36px;
    height: 36px;
    border-radius: 50%;
    background: var(--orange);
  }
  .brand-name {
    color: var(--white);
    font-size: 84px;
    font-weight: 500;
    letter-spacing: 3px;
    line-height: 1;
  }
  .taglines {
    position: absolute;
    top: 222px;
    left: 350px;
    width: 490px;
    text-align: center;
    color: var(--orange);
    font-size: 46px;
    line-height: 58px;
  }
  .event-title {
    position: absolute;
    top: 422px;
    left: 14px;
    margin: 0;
    color: var(--orange);
    font-size: 54px;
    font-weight: 400;
    line-height: 54px;
    letter-spacing: -0.5px;
  }
  .keywords {
    position: absolute;
    top: 477px;
    left: 5px;
    color: var(--ink);
    font-size: 34px;
    line-height: 44px;
  }
  .keywords .line-one { padding-left: 94px; }
  .details {
    position: absolute;
    top: 743px;
    left: 21px;
    color: var(--white);
    font-size: 29px;
    line-height: 40px;
  }
  .details .time { margin-top: 5px; padding-left: 3px; }
  .details .address { margin-top: 2px; padding-left: 5px; line-height: 34px; }
  .hl { color: var(--orange); }
  .contact {
    position: absolute;
    top: 1007px;
    left: 0;
    width: 812px;
    text-align: center;
    color: var(--white);
    font-size: 28px;
    line-height: 34px;
  }
</style>
</head>
<body>
<main class="flyer">
  <svg class="backdrop" viewBox="0 0 1619 2296" preserveAspectRatio="none" aria-hidden="true">
    <defs>
      <linearGradient id="band-gradient" x1="0" y1="0" x2="1" y2="1">
        <stop offset="0" stop-color="#fb8c00"/>
        <stop offset="0.55" stop-color="#9c7228"/>
        <stop offset="1" stop-color="#5a5a3f"/>
      </linearGradient>
      <linearGradient id="light-gradient" x1="0" y1="0" x2="0" y2="1">
        <stop offset="0" stop-color="#ffffff"/>
        <stop offset="0.4" stop-color="#ffffff"/>
        <stop offset="0.72" stop-color="#9fb3c2"/>
        <stop offset="1" stop-color="#2d5a79"/>
      </linearGradient>
      <linearGradient id="red-gradient" x1="0" y1="0" x2="0" y2="1">
        <stop offset="0" stop-color="#8b0000"/>
        <stop offset="0.45" stop-color="#5a0000"/>
        <stop offset="1" stop-color="#000000"/>
      </linearGradient>
    </defs>
    <rect width="1619" height="2296" fill="#003a5c"/>
    <path d="M0,190 C200,380 400,520 700,600 C1000,680 1300,760 1619,1012 L1619,2296 L0,2296 Z" fill="url(#band-gradient)"/>
    <path d="M0,370 C250,560 450,690 800,750 C1150,810 1400,870 1619,1018 L1619,2296 L0,2296 Z" fill="url(#light-gradient)"/>
    <path d="M0,1100 C180,1210 380,1260 640,1205 C900,1150 1100,1060 1300,1078 C1450,1090 1550,1125 1619,1158 L1619,2296 L0,2296 Z" fill="url(#red-gradient)"/>
  </svg>

  <div class="brand">
    <span class="brand-dot"></span>
    <span class="brand-name">TOLVEX</span>
  </div>

  <div class="taglines">
    <div>A one day prayer retreat.</div>
    <div>Jesus Chris is Lord</div>
  </div>

  <h1 class="event-title">Radiant Harvest Worship Day</h1>

  <div class="keywords">
    <div class="line-one">Prayer, Sharing the Word,</div>
    <div>Panel discussion prophecy, Impartation.</div>
  </div>

  <div class="details">
    <div class="date">Tuesday July <span class="hl">2</span>nd, <span class="hl">2019</span></div>
    <div class="time"><span class="hl">11:00</span>AM – <span class="hl">7:00</span>PM</div>
    <div class="address">Belmora Hotel, <span class="hl">4875</span> Wexley<br>Avenue, Portland, Maine <span class="hl">04102</span> (Room: Juniper)</div>
  </div>

  <div class="contact">
    <div>Contact info:</div>
    <div>www.tolvex.org</div>
    <div>Phone: <span class="hl">207 555 3184</span></div>
    <div>Email: <span class="hl">contact@brookhavenfold.org</span></div>
  </div>
</main>
</body>
</html>
```